Corporate website design needed

We need a Contemporary Industrial/Tech/Logistics Website design to match our logistic client's business. Our client consults and build logistics solutions that they manage but they are not a typical 3PL (3rd party logistics company) which is primarily engaged in moving boxes.
PSD file only for now, home and default templates.
COMPANY CHARACTER
DESIGN LOOK AND FEEL
• The design should also be modern and visually well organized — employing a combination of visual devices and info graphics. Keep it light and not too heavy but strong/ professional. And unique.
• The design should go beyond the typical industrial pick and pack 3PL representing [Logistics Company] as a High Tech/IT logistics company.
Some examples although these are not right for this client because they have much more content and present themselves more as a 3pl.
http://www.vobrelink-hub.example/ (More right then wrong - Like this but simplified)
http://www.durmaxfreight.example (Ugly)
http://www.tpwallerton.example (More right then wrong but different focus)
http://www.pelhamrye.example/ Too 3PL trucking… We want a bit ore high level approach
The difference, the design should be a fusion in core concepts that culminate in a design which implies the following attributes. Tech (Big data / analytics / software), Consultancy (Solutions, SME, Leader), 3PL Industry vertical solutions.
NOTE: The visualization of “tech” is not “1” and “0”, but more “software and analytics” Perhaps more like www.navimetra.example.
• They need to be seen as a solutions provider in Logistics and as in Subject matter experts
TONE
The tone needs to exude professionalism, expertise, though leadership along with technical and executional excellence.
Experienced
Knowledgeable
Confident
Determined
Straightforward
WEBSITE OBJECTIVES
• Focus C-Suite executives and logistics managers’ attention on [Logistics Company]s commanding knowledge and expertise, and unique approach to supply chain solutions producing more RFP wins
• Create an easy to scan design which decreases the reliance on text through featured text, summaries, and smaller “chunked” size bits of information.
• Convey [Logistics Company] as high-tech 3PL solutions developer and services provider with a ‘high-touch’ consultative approach.
• Showcase [Logistics Company]’s value propositions. (See Slider Content)
• Showcase [Logistics Company]’s expertise in logistical analytics.
• Gain recognition as an industry leader in evolutionary new space (supply chain 2.0)
WEBSITE STRATEGY
• Reduce reliance on text (at least within initial entry points for each section)
• Typography: Watch text line lengths and readability, bolder fonts. NO SERIFS
• Generally, create a click-through format so that users who want more details can find it, and those who don’t can get a snapshot without clicking through.
• Increase visual content through info graphics and some dynamic content, photography
• Better utilize the space on each page (e.g., add visual interest, photography and iconography where appropriate to break up copy blocks and maintain readable line lengths).
COLOR SCHEME
• Create a more engaging color scheme (the logo will remain the same under all circumstances).
• Red / grayscale may work…. Not too dark or heavy. Not too much red. Ex. quiltora.example
• Also try blues and greys. They seem to like that. Open to suggestions but don’t get to crazy. Red is in their logo but too much may be a problem.
PHOTOGRAPHY
Yes. And I will upload some.
If you pick photography please be sure to note Which stock house used and the image number!
CONTENT
The content will be presented in a more hierarchical format — with lead-ins, paragraph and section headers and navigational cues to expand lengthier content allowing the visitor to more easily scan the website. No case studies, No Social media, News while on the home page should not be over emphasized. They don't post a lot so it gets dated quickly ...
I will be uploading a wire frame and other elements.
NOTE: I uploaded my EXAMPLE mock up which is close but not close enough.
I am not a great designer. So I am looking for an alternative that exceed my design ability! These examples show the basic layout but I really want some varied alternatives.
The colors are inconsistent and type not quite right. The grey bar at top is not right and should probably go away.
Please pull the basic elements in the example together into a great design.
If you have questions please contact me.
i will upload some photography tomorrow that may be of use.
Thanks!
Updates
Hi All,
We are still evaluating the submitted designs. Sorry for the delay.
Target Market(s)
This website is primarily a validation website. Few new customers will search and find them as such...
The site should be Focused on C-Suite executives and logistics managers’ attention on [Logistics Company]s commanding knowledge and expertise, and unique approach to supply chain solutions producing more RFP wins
Industry/Entity Type
Business
Font styles to use
Requirements
Must have
- Slide show, Clearly explain who they are and what they do.
Create an easy to scan design which decreases the reliance on text through featured text, summaries, and smaller “chunked” size bits of information.
Convey [Logistics Company] as high-tech 3PL solutions developer and services
provider with a ‘high-touch’ consultative approach.
Should not have
- No Ads space
No Social media
Not too cluttered. Keep it clean.

```html
<!DOCTYPE html>
<html lang="en">
<head>
<meta charset="utf-8">
<title>Kestrel Ridge Logistics</title>
<link href="https://fonts.googleapis.com/css2?family=Nunito+Sans:wght@300;400;600;700;800&display=swap" rel="stylesheet">
<style>
:root{
  --red:#e8434c;
  --red-dark:#c8102e;
  --ink:#4a4f57;
  --muted:#7d8591;
  --pink-bg:#fdf3f3;
  --footer:#2e363d;
  --footer-deep:#262d33;
  --footer-text:#9aa2ab;
  --line:#e5e5e5;
}
*{margin:0;padding:0;box-sizing:border-box}
html,body{width:1024px;height:1200px;overflow:hidden;background:#fff}
body{font-family:"Nunito Sans",Arial,sans-serif;color:var(--ink);position:relative}
.abs{position:absolute}

.topbar{top:0;left:0;width:1024px;height:31px;border-bottom:1px solid var(--line);font-size:9px;color:var(--muted)}
.topbar a{position:absolute;top:10px;color:var(--muted);text-decoration:none}
.topbar .divider{position:absolute;left:750px;top:8px;width:1px;height:14px;background:#ccc}
.topbar .sales{left:779px;top:9px;display:flex;align-items:center;gap:8px;position:absolute}

.header{top:31px;left:0;width:1024px;height:73px;border-bottom:1px solid #eee}
.brand{position:absolute;left:121px;top:22px;display:flex;align-items:center;gap:10px}
.brand .dot{width:26px;height:26px;border-radius:50%;background:var(--red-dark)}
.brand span{font-size:17px;font-weight:800;letter-spacing:3px;color:#2b2f33;text-transform:uppercase}
.nav{position:absolute;top:29px;font-size:13px;font-weight:700;color:#6a7079;letter-spacing:.2px}
.search{position:absolute;left:884px;top:28px}

.hero{top:104px;left:0;width:1024px;height:338px;background:linear-gradient(180deg,#f2f1f1 0,#e9e7e7 100%)}
.hero-panel{top:104px;left:634px;width:269px;height:338px;background:rgba(85,80,82,.95);color:#fff}
.hero-panel h1{position:absolute;left:34px;top:82px;font-weight:300;font-size:27px;line-height:40px}
.hero-panel h1 b{color:var(--red);font-weight:700}
.dots{position:absolute;left:40px;top:301px;display:flex;gap:8px;align-items:center}
.dots i{width:8px;height:8px;border-radius:50%;background:#e6e6e6;display:block}
.dots i.on{width:11px;height:11px;background:var(--red-dark);border:2px solid #fff}

.section-title{top:476px;left:120px;font-size:18px;font-weight:700;color:#4f555c}
.title-rule{top:485px;left:366px;width:536px;height:4px;border-top:1px dotted #bbb;border-bottom:1px dotted #bbb}
.intro{top:514px;left:120px;width:240px;font-size:12.4px;line-height:19px;color:var(--muted)}
.service{display:flex;align-items:center;gap:11px;font-size:12.4px;font-weight:700;line-height:19px;color:#444a51}
.service .ico{width:43px;height:43px;background:linear-gradient(135deg,#f0646b,#e23c45);display:flex;align-items:center;justify-content:center;flex:none}

.band{top:692px;left:0;width:1024px;height:290px;background:var(--pink-bg);border-top:1px solid #eee}
.video{top:722px;left:121px;width:378px;height:227px;background:linear-gradient(180deg,#4a535c 0,#2f3840 60%,#20272d 100%)}
.video .bar{position:absolute;left:0;bottom:0;width:100%;height:17px;background:#1b1f23}
.video .track{position:absolute;left:0;bottom:17px;width:100%;height:3px;background:#555}
.video .track i{display:block;width:16px;height:3px;background:var(--red-dark)}
.points{top:724px;left:529px;width:345px}
.points h3{font-size:12.4px;font-weight:700;color:#4a4f57;margin-bottom:5px}
.points p{font-size:12.4px;line-height:19px;color:var(--muted);margin-bottom:23px}

.footer{top:982px;left:0;width:1024px;height:188px;background:var(--footer);color:var(--footer-text);font-size:10px}
.footer h4{position:absolute;color:#fff;font-size:10.5px;font-weight:600}
.fbrand{position:absolute;left:130px;top:40px;display:flex;align-items:center;gap:8px}
.fbrand .dot{width:20px;height:20px;border-radius:50%;background:#fff}
.fbrand span{color:#fff;font-weight:800;font-size:13px;letter-spacing:2px}
.post{position:absolute;left:331px;display:flex;gap:11px;line-height:16px}
.post .thumb{width:43px;height:43px;background:linear-gradient(135deg,#8a939c,#4b545c);flex:none}
.post small{font-size:10px;color:#7c858e}
.sub{position:absolute;left:534px;top:107px;display:flex;height:30px}
.sub .field{width:129px;background:#232a30;color:#cfd4d9;font-size:10px;padding:9px 11px}
.sub .btn{width:70px;background:var(--red-dark);color:#fff;font-size:10.5px;text-align:center;padding-top:8px}
.contact{position:absolute;left:752px;display:flex;gap:10px;align-items:flex-start;line-height:16px}
.bottombar{top:1170px;left:0;width:1024px;height:30px;background:var(--footer-deep);color:#7c858e;font-size:10px}
.bottombar span{position:absolute;top:9px}
</style>
</head>
<body>

<div class="abs topbar">
  <a style="left:535px">Company</a>
  <a style="left:617px">Careers</a>
  <a style="left:689px">Contact</a>
  <div class="divider"></div>
  <div class="sales">
    <svg width="13" height="13" viewBox="0 0 24 24"><path fill="#c8102e" d="M6.6 10.8a15 15 0 0 0 6.6 6.6l2.2-2.2c.3-.3.7-.4 1-.2 1.1.4 2.3.6 3.6.6.6 0 1 .4 1 1V20c0 .6-.4 1-1 1A17 17 0 0 1 3 4c0-.6.4-1 1-1h3.5c.6 0 1 .4 1 1 0 1.3.2 2.5.6 3.6.1.3 0 .7-.2 1z"/></svg>
    <span>Sales: +1-555-014-2738</span>
  </div>
</div>

<header class="abs header">
  <div class="brand"><div class="dot"></div><span>Kestrel Ridge</span></div>
  <div class="nav" style="left:519px">SOLUTIONS</div>
  <div class="nav" style="left:646px">OUR PROCESS</div>
  <div class="nav" style="left:791px">INDUSTRIES</div>
  <svg class="search" width="18" height="18" viewBox="0 0 24 24"><circle cx="10" cy="10" r="6.5" fill="none" stroke="#9aa0a7" stroke-width="2.6"/><path d="M15 15l6 6" stroke="#9aa0a7" stroke-width="3" stroke-linecap="round"/></svg>
</header>

<div class="abs hero" role="img" aria-label="Hero photograph: one red umbrella standing out among many white umbrellas"></div>
<div class="abs hero-panel">
  <h1>A <b>New Way</b> To<br>Think About<br>Supply Chain<br>Transformation</h1>
  <div class="dots"><i></i><i class="on"></i><i></i><i></i></div>
</div>

<h2 class="abs section-title">Infrastructure Solutions</h2>
<div class="abs title-rule"></div>
<p class="abs intro">Kestrel Ridge manages complexity, provides data-driven solutions and implements innovation and actionable strategies that delivers business results.</p>

<div class="abs service" style="left:390px;top:518px">
  <div class="ico"><svg width="14" height="16" viewBox="0 0 14 16"><rect x="2" y="1" width="10" height="14" fill="none" stroke="#fff" stroke-width="1.4"/><path d="M4.5 4h2M8 4h2M4.5 7h2M8 7h2M4.5 10h2M8 10h2" stroke="#fff" stroke-width="1.2"/></svg></div>
  <div>Material Management<br>&amp; Factory Support</div>
</div>
<div class="abs service" style="left:658px;top:518px">
  <div class="ico"><svg width="16" height="14" viewBox="0 0 16 14"><path d="M1 1h3l1.5 7h8l1.5-5H5" fill="#fff" stroke="#fff" stroke-width="1.2"/><circle cx="6" cy="11.5" r="1.4" fill="#fff"/><circle cx="12" cy="11.5" r="1.4" fill="#fff"/></svg></div>
  <div>Retail and e-Commerce<br>Distribution</div>
</div>
<div class="abs service" style="left:121px;top:612px">
  <div class="ico"><svg width="14" height="16" viewBox="0 0 14 16"><path d="M2 1v5c0 1 .8 2 2 2v7M4 1v5M6 1v5c0 1-.8 2-2 2M11 1c-2 1-2 4-2 6h2v8" fill="none" stroke="#fff" stroke-width="1.5"/></svg></div>
  <div>Aftermarket Support</div>
</div>
<div class="abs service" style="left:390px;top:612px">
  <div class="ico"><svg width="17" height="14" viewBox="0 0 17 14"><ellipse cx="7" cy="6" rx="6" ry="4.5" fill="none" stroke="#fff" stroke-width="1.5"/><path d="M4 10l-1 3 3-2" fill="#fff"/><path d="M13 4c2 .8 3 2 3 3.5 0 1.2-.8 2.3-2 3l1 2-3-1.3" fill="none" stroke="#fff" stroke-width="1.3"/></svg></div>
  <div>Aftermarket Support</div>
</div>
<div class="abs service" style="left:658px;top:612px">
  <div class="ico"><svg width="16" height="14" viewBox="0 0 16 14"><rect x="6" y="0" width="4" height="4" fill="#fff"/><rect x="0" y="10" width="4" height="4" fill="#fff"/><rect x="6" y="10" width="4" height="4" fill="#fff"/><rect x="12" y="10" width="4" height="4" fill="#fff"/><path d="M8 4v6M2 10V7h12v3" fill="none" stroke="#fff" stroke-width="1.3"/></svg></div>
  <div>Supply Chain<br>Transformation Services</div>
</div>

<div class="abs band"></div>
<div class="abs video" role="img" aria-label="Video still of modern glass office towers at dusk">
  <div class="track"><i></i></div>
  <div class="bar"></div>
</div>
<div class="abs points">
  <h3>A DIFFERENT INCENTIVE</h3>
  <p>We commit our own capital and resources to align with our clients' goals</p>
  <h3>A DIFFERENT APPROACH</h3>
  <p>Unlike consultants, we implement and operate the solutions we design</p>
  <h3>A DIFFERENT LEVEL OF COMMITMENT</h3>
  <p>We guarantee business performance for our clients by investing in and executing the solutions we design.</p>
</div>

<footer class="abs footer">
  <div class="fbrand"><div class="dot"></div><span>KESTREL RIDGE</span></div>
  <p style="position:absolute;left:130px;top:126px;width:175px;line-height:16px">Donec volutpat, mi vel egestas eleifend, dolor arcu iaculis nunc. Fusce gravida tortor felis, ac dictum risus</p>

  <h4 style="left:331px;top:27px">Recent Post</h4>
  <div class="post" style="top:62px"><div class="thumb" role="img" aria-label="Thumbnail of two colleagues reviewing work"></div><div>Fusce gravida tortor felis,<br>ac dictum risus sagittis<br><small>October 15, 2013</small></div></div>
  <div class="post" style="top:124px"><div class="thumb" role="img" aria-label="Thumbnail of a hand using a tablet"></div><div>Fusce gravida tortor felis,<br>ac dictum risus sagittis<br><small>October 15, 2013</small></div></div>

  <h4 style="left:534px;top:25px">Newsletter</h4>
  <p style="position:absolute;left:534px;top:60px;width:180px;line-height:18px">Ipsum dolor sit amet, teft consecte tur adipiscing elit ut eunt.</p>
  <div class="sub"><div class="field">Email Address</div><div class="btn">Subscribe</div></div>

  <h4 style="left:752px;top:28px">Contact Details</h4>
  <div class="contact" style="top:62px"><svg width="13" height="13" viewBox="0 0 24 24"><path fill="#7c858e" d="M6.6 10.8a15 15 0 0 0 6.6 6.6l2.2-2.2c.3-.3.7-.4 1-.2 1.1.4 2.3.6 3.6.6.6 0 1 .4 1 1V20c0 .6-.4 1-1 1A17 17 0 0 1 3 4c0-.6.4-1 1-1h3.5c.6 0 1 .4 1 1 0 1.3.2 2.5.6 3.6.1.3 0 .7-.2 1z"/></svg><span>+1-555-019-4410</span></div>
  <div class="contact" style="top:86px"><svg width="13" height="13" viewBox="0 0 14 12"><rect x="1" y="1" width="12" height="10" fill="none" stroke="#7c858e" stroke-width="1.3"/><path d="M1 1l6 5 6-5" fill="none" stroke="#7c858e" stroke-width="1.3"/></svg><span>hello@kestrelridge.example</span></div>
  <div class="contact" style="top:110px"><svg width="13" height="15" viewBox="0 0 12 16"><path d="M6 0a6 6 0 0 0-6 6c0 4 6 10 6 10s6-6 6-10a6 6 0 0 0-6-6z" fill="#7c858e"/><circle cx="6" cy="6" r="2.2" fill="#2e363d"/></svg><span>Your Address, Your Country<br>Your Zip Code</span></div>
</footer>

<div class="abs bottombar">
  <span style="left:130px">Copyright © 2014 - Kestrel Ridge Logistics. All Rights Reserved.</span>
  <span style="left:791px">Privacy Policy</span>
  <span style="left:882px">Sitemap</span>
</div>

</body>
</html>
```